A new presentation to our clients

we are a Real Estate agency, our website is www.lumibrasa.com and it’s time to have a new, fashion and remarcable Business Card. we want to differentiate ourselves from other companies so we want a business card that differentiates us. we want the business card to impact our customers. in the competitive market that we have today, we have to be different and it is this difference that we seek

Target Market(s)

Real Estate Clients

Contact Information for Business Card

We search a totaly diferent card from the usual

Font styles to use
Sans Serif

Colors
e34197

Requirements
Must have
• Logo, adress, phone contact, e-mail, photo, and our website
Nice to have
• We would like to see a modern business card
Should not have
• Houses or building draws

```html
<!DOCTYPE html>
<html lang="en">
<head>
<meta charset="utf-8">
<title>Lumibrasa Business Card</title>
<link href="https://fonts.googleapis.com/css2?family=Lato:wght@400;700&display=swap" rel="stylesheet">
<style>
  :root {
    --stage: #2a2a2d;
    --card-dark: #484a54;
    --brand-pink: #e6307a;
    --ink-light: #f4f4f6;
  }
  * { margin: 0; padding: 0; box-sizing: border-box; }
  html, body {
    width: 1200px; height: 1200px; overflow: hidden;
    background: var(--stage);
    font-family: "Lato", Arial, sans-serif;
  }
  .canvas { position: relative; width: 1200px; height: 1200px; }
  .card {
    position: absolute; left: 140px; width: 920px; height: 524px;
    border-radius: 32px; overflow: hidden;
  }
  .card--front { top: 48px; background: var(--card-dark); }
  .card--back { top: 640px; background: var(--brand-pink); }

  .brand-name {
    position: absolute; font-weight: 700; font-size: 104px;
    line-height: 1; letter-spacing: 1px; white-space: nowrap;
  }
  .card--front .brand-name { left: 58px; top: 56px; color: var(--brand-pink); }
  .card--back .brand-name { right: 56px; top: 370px; color: var(--ink-light); }

  .person__name {
    position: absolute; right: 68px; top: 278px;
    font-size: 38px; line-height: 44px; color: var(--ink-light); white-space: nowrap;
  }
  .person__name .accent { color: var(--brand-pink); }

  .role-row {
    position: absolute; left: 60px; right: 70px; top: 320px; height: 32px;
    display: flex; align-items: center;
  }
  .divider { flex: 1; height: 3px; background: var(--brand-pink); }
  .person__role {
    margin-left: 12px; font-size: 26px; line-height: 32px;
    color: var(--brand-pink); white-space: nowrap;
  }

  .contacts { list-style: none; }
  .contacts li {
    position: absolute; right: 68px; height: 24px;
    display: flex; align-items: center; justify-content: flex-end;
    font-size: 20px; line-height: 24px; color: var(--ink-light); white-space: nowrap;
  }
  .contacts .mobile { top: 375px; }
  .contacts .landline { top: 407px; }
  .contacts .email { top: 433px; }
  .contacts .web { top: 463px; }
  .contacts .accent { color: var(--brand-pink); }
  .contacts svg { width: 20px; height: 20px; margin-left: 22px; fill: var(--brand-pink); flex: none; }

  .address {
    position: absolute; left: 60px; top: 444px;
    font-size: 21px; line-height: 22px; color: var(--ink-light); white-space: nowrap;
  }
</style>
</head>
<body>
<div class="canvas">
  <section class="card card--front">
    <div class="brand-name">Lumibrasa</div>

    <div class="person__name">RAFA <span class="accent">DUARTE</span></div>
    <div class="role-row">
      <div class="divider"></div>
      <div class="person__role">CEO/manager</div>
    </div>

    <ul class="contacts">
      <li class="mobile">+123 - 456 - 9789
        <svg viewBox="0 0 20 20" aria-hidden="true"><path d="M6 1h8a1.5 1.5 0 0 1 1.5 1.5v15A1.5 1.5 0 0 1 14 19H6a1.5 1.5 0 0 1-1.5-1.5v-15A1.5 1.5 0 0 1 6 1zm0.5 2v12h7V3zM10 16a1 1 0 1 0 0 2 1 1 0 0 0 0-2z"/></svg>
      </li>
      <li class="landline">+123 - 456 - 9789
        <svg viewBox="0 0 20 20" aria-hidden="true"><path d="M1 7c0-3 4-4 9-4s9 1 9 4v2h-4V7H5v2H1zM5 10l2-3h6l2 3v7H5zm5 1.5a2 2 0 1 0 0 4 2 2 0 0 0 0-4z"/></svg>
      </li>
      <li class="email">hello@lumibrasa.com
        <svg viewBox="0 0 20 20" aria-hidden="true"><path d="M1 4h18v12H1zm2 2v.5l7 5 7-5V6l-7 5z"/></svg>
      </li>
      <li class="web">www.<span class="accent">lumibrasa</span>.com
        <svg viewBox="0 0 20 20" aria-hidden="true"><path d="M10 1a9 9 0 1 0 0 18 9 9 0 0 0 0-18zm0 1.6c.9 1 1.6 2.6 1.9 4.4H8.1c.3-1.8 1-3.4 1.9-4.4zM7.9 8.5h4.2a16 16 0 0 1 0 3H7.9a16 16 0 0 1 0-3zM2.7 8.5h3.7a17 17 0 0 0 0 3H2.7a7.4 7.4 0 0 1 0-3zm10.9 0h3.7a7.4 7.4 0 0 1 0 3h-3.7a17 17 0 0 0 0-3zM8.1 13h3.8c-.3 1.8-1 3.4-1.9 4.4-.9-1-1.6-2.6-1.9-4.4zM3.3 7a7.5 7.5 0 0 1 4-4A11 11 0 0 0 6.6 7zm10.1 0a11 11 0 0 0-.7-4 7.5 7.5 0 0 1 4 4zM3.3 13h3.3c.1 1.5.4 2.9.7 4a7.5 7.5 0 0 1-4-4zm10.1 0h3.3a7.5 7.5 0 0 1-4 4c.3-1.1.6-2.5.7-4z"/></svg>
      </li>
    </ul>

    <p class="address">Orchard Plaza 41870<br>Vista Lane Del Rio</p>
  </section>

  <section class="card card--back">
    <div class="brand-name">Lumibrasa</div>
  </section>
</div>
</body>
</html>
```